A Techincal Author needs a site to promote his Programming Books

The StudyAlong series is a collection of books focusing on building the same app with different technologies. The purpose of this project is to design a web site home page that can be used to sell the books.

Expected Deliverables
• StudyAlong Logo as Illustrator file
• Master graphic design files for any relevant web assets
• HTML and CSS for home page, if applicable

Target Market(s)

The target market for our series is web programmers. They are people who have some experience, but want to learn a new tool. Programmers are analytical, logical people who like structure in the things they do.

Here are some things our customers like:

• Chirply / Postbox
• Crown of Ashes / Hollow Tide / Salt Hollow
• SmartPhones, Tablets, Stridelets, and other tech gadgets.

The design should try to speak to that market.

Requirements
Must have
• The primary tasks for this project are:
• 1) Create "Study Along" Logo.
• * All “Tallowick” properties use a similar logo approach, with the Tallowick ball icon on the left, a reflection below it. The company name is on the right, roughly the same size as the ball icon. A tag line underneath the company name, roughly the same size as the reflection.
• * Company Name: Study Along
• * Tagline: Knowledge to Boost Your Career
• * Logo color is up to the discretion of the designer, but should be compatible with the site design.
• * Sample Logos for other Tallowick properties in Illustrator format are available as attachments to this project.
• 2) Design the Study Along Home Page.
• The home page should follow this format:
• * Logo
• * Nav Bar
• • Buy (The Home Page)
• • About
• • Contact
• * Main Content
• • Home page content detailed in attachment
• * Footer
• • Copyright notice
• • Links to other stuff we do ( net-pivot.example | marlonpeake.example | BeyondTheGrid.example )
Nice to have
• It would be nice to have a book as part of the home page content.
Should not have
• Please do not use the same color scheme as BeyondTheGrid.example or Plumvane.example or QueryTheMaven.example

```html
<!DOCTYPE html>
<html lang="en">
<head>
<meta charset="utf-8">
<title>StudyAlong — Knowledge to Boost Your Career</title>
<link href="https://fonts.googleapis.com/css2?family=Open+Sans:wght@300;400;600;700&display=swap" rel="stylesheet">
<style>
:root{
  --brand-red:#b5272d;
  --brand-gold:#f6a914;
  --band-gold:#fbb316;
  --ink:#444;
  --ink-soft:#666;
  --line:#dcdcdc;
  --dark:#1c1c1c;
  --button:#333;
  --white:#fff;
}
*{box-sizing:border-box;margin:0;padding:0}
html,body{width:1074px;height:1200px;overflow:hidden;background:var(--white);font-family:"Open Sans",Arial,sans-serif;color:var(--ink)}
.site-header{height:81px;position:relative}
.brand{position:absolute;left:118px;top:16px;display:flex;align-items:center;gap:10px}
.brand-dot{width:34px;height:34px;border-radius:50%;background:var(--brand-red)}
.brand-name{font-size:38px;font-weight:600;color:var(--brand-gold);letter-spacing:-0.5px;line-height:44px}
.main-nav{position:absolute;right:118px;top:34px;display:flex;gap:31px;font-size:12px}
.main-nav a{color:var(--ink);text-decoration:none}
.main-nav a.active{color:var(--brand-red)}
.hero{position:relative;height:326px;background:linear-gradient(100deg,#eeeeee 0%,#f6f6f6 40%,#dadada 55%,#ececec 75%,#e2e2e2 100%)}
.hero-title{position:absolute;left:120px;top:129px;font-size:29px;font-weight:700;line-height:36px;color:var(--ink)}
.hero-dots{position:absolute;left:501px;top:296px;display:flex;gap:13px}
.hero-dots span{width:8px;height:8px;border-radius:50%;background:var(--white)}
.hero-dots span.current{background:transparent;border:1.5px solid var(--white)}
.signup{height:143px;background:var(--band-gold);text-align:center;padding-top:25px}
.signup h2{color:var(--white);font-size:29px;font-weight:700;line-height:36px}
.signup-form{display:flex;justify-content:center;gap:7px;margin-top:12px}
.signup-form .field{width:215px;height:39px;background:var(--white);font-size:11.5px;color:var(--ink-soft);text-align:left;padding:12px 16px}
.signup-form .submit{width:72px;height:39px;background:var(--button);color:var(--white);font-size:12px;font-weight:600;line-height:39px}
.books{position:absolute;left:117px;top:598px;width:840px}
.panel{border:1px solid var(--line);margin-bottom:16px;box-shadow:0 1px 2px rgba(0,0,0,.08)}
.panel-head{height:48px;display:flex;align-items:center;background:linear-gradient(#f7f7f7,#ececec)}
.panel-toggle{width:44px;height:48px;border-right:1px solid var(--line);display:flex;align-items:center;justify-content:center}
.panel-title{flex:1;padding-left:16px;font-size:17px;font-weight:300;color:var(--ink)}
.panel-link{padding-right:12px;font-size:12px;color:var(--ink-soft);display:flex;align-items:center;gap:6px}
.panel-body{padding:17px 18px 16px;border-top:1px solid var(--line)}
.price-table{width:100%;border-collapse:separate;border-spacing:0 2px;font-size:13px}
.price-table td{height:39px;border:1px solid #e6e6e6;border-left:none;text-align:center;color:var(--ink-soft)}
.price-table td:first-child{border-left:1px solid #e6e6e6;text-align:left;padding-left:17px;width:252px}
.price-table .edition,.price-table .price{color:var(--brand-gold);font-weight:600}
.price-table .price{width:147px}
.price-table .store{width:241px}
.store-mark{display:inline-flex;align-items:center;gap:4px;font-weight:700;font-size:10px;color:var(--ink);margin-left:6px}
.store-mark i{width:10px;height:10px;border:1.5px solid var(--brand-red);display:inline-block}
.partners{position:absolute;left:117px;top:1030px;width:840px;display:flex;align-items:center}
.partners-label{font-size:13px;color:var(--ink-soft);width:141px}
.partner{display:flex;align-items:center;gap:5px;font-size:19px;font-weight:600;color:#555;width:258px}
.partner b{width:14px;height:14px;border-radius:50%;background:#777;display:inline-block}
.site-footer{position:absolute;left:0;top:1114px;width:1074px;height:86px;background:var(--dark);text-align:center;color:#aaa;font-size:11px}
.footer-links{margin-top:24px}
.footer-links a{color:#aaa;text-decoration:none;margin:0 6px}
.copyright{margin-top:11px}
</style>
</head>
<body>
<header class="site-header">
  <div class="brand"><span class="brand-dot"></span><span class="brand-name">StudyAlong</span></div>
  <nav class="main-nav"><a class="active" href="#">HOME</a><a href="#">ABOUT US</a><a href="#">CONTACT US</a></nav>
</header>

<section class="hero" role="img" aria-label="Photo of a person typing on a laptop on a white wooden desk with glasses, a tablet and a cup of tea">
  <h1 class="hero-title">Knowledge to<br>Boost Your Career</h1>
  <div class="hero-dots"><span class="current"></span><span></span><span></span><span></span></div>
</section>

<section class="signup">
  <h2>Sign up for a Free Sample</h2>
  <div class="signup-form"><div class="field">First Name</div><div class="field">Email Address</div><div class="submit">SUBMIT</div></div>
</section>

<main class="books">
  <div class="panel">
    <div class="panel-head">
      <div class="panel-toggle"><svg width="14" height="14" viewBox="0 0 14 14"><circle cx="7" cy="7" r="7" fill="#777"/><path d="M7 3.5 10 7H8v3.5H6V7H4z" fill="#fff"/></svg></div>
      <div class="panel-title">Angulon 1.5 &amp; Scaffold</div>
      <div class="panel-link"><svg width="11" height="11" viewBox="0 0 11 11"><path d="M4 7 7 4M3 5 1.5 6.5a2 2 0 0 0 3 3L6 8M5 3l1.5-1.5a2 2 0 0 1 3 3L8 6" stroke="#666" stroke-width="1.3" fill="none"/></svg>VIEW APP LINK</div>
    </div>
    <div class="panel-body">
      <table class="price-table">
        <tr><td class="edition">With Mock Services</td><td class="price">$5.99</td><td class="store">Buy from Us <span class="store-mark"><i></i>Cartlyne</span></td><td>Buy from <span class="store-mark">Parcelora</span></td></tr>
        <tr><td class="edition">With NodeWeave Services</td><td class="price">$5.99</td><td class="store">Buy from Us <span class="store-mark"><i></i>Cartlyne</span></td><td>Buy from <span class="store-mark">Parcelora</span></td></tr>
        <tr><td class="edition">With FrostMelt Services</td><td class="price">$5.99</td><td class="store">Buy from Us <span class="store-mark"><i></i>Cartlyne</span></td><td>Buy from <span class="store-mark">Parcelora</span></td></tr>
        <tr><td class="edition">Buy Them All</td><td class="price">$9.99</td><td class="store">Buy from Us <span class="store-mark"><i></i>Cartlyne</span></td><td>Buy from <span class="store-mark">Parcelora</span></td></tr>
      </table>
    </div>
  </div>
  <div class="panel">
    <div class="panel-head">
      <div class="panel-toggle"><svg width="14" height="14" viewBox="0 0 14 14"><circle cx="7" cy="7" r="7" fill="#777"/><path d="M7 10.5 10 7H8V3.5H6V7H4z" fill="#fff"/></svg></div>
      <div class="panel-title">Angulon 2 &amp; Scaffold</div>
      <div class="panel-link"><svg width="11" height="11" viewBox="0 0 11 11"><path d="M4 7 7 4M3 5 1.5 6.5a2 2 0 0 0 3 3L6 8M5 3l1.5-1.5a2 2 0 0 1 3 3L8 6" stroke="#666" stroke-width="1.3" fill="none"/></svg>VIEW APP LINK</div>
    </div>
  </div>
  <div class="panel">
    <div class="panel-head">
      <div class="panel-toggle"><svg width="14" height="14" viewBox="0 0 14 14"><circle cx="7" cy="7" r="7" fill="#777"/><path d="M7 10.5 10 7H8V3.5H6V7H4z" fill="#fff"/></svg></div>
      <div class="panel-title">Quivrel</div>
      <div class="panel-link"><svg width="11" height="11" viewBox="0 0 11 11"><path d="M4 7 7 4M3 5 1.5 6.5a2 2 0 0 0 3 3L6 8M5 3l1.5-1.5a2 2 0 0 1 3 3L8 6" stroke="#666" stroke-width="1.3" fill="none"/></svg>VIEW APP LINK</div>
    </div>
  </div>
</main>

<section class="partners">
  <div class="partners-label">Partners</div>
  <div class="partner"><b></b>BeyondTheGrid</div>
  <div class="partner"><b></b>Tallowick Consulting</div>
  <div class="partner"><b></b>Plumvane</div>
</section>

<footer class="site-footer">
  <div class="footer-links"><a href="#">Home</a>|<a href="#">About Us</a>|<a href="#">Contact Us</a></div>
  <div class="copyright">Copyright © 2016 StudyAlong. All rights reserved.</div>
</footer>
</body>
</html>
```